Bramwell Specialty Coffee needs a Packaging design

We need packaging design for coffee that suits our brand identity, that is the best quality in Mexico.
We only sell mexican coffee with Q scores above 80
We are evaluating 3 types of packaging: Bag, Box and Cillinder can
The specific package format will be decided based on the designs that we get.

Target Market(s)

Coffee experts and enthusiast.
People that relate the Coffee consumption and experience with wine tasting and Bon Vivant way

Requirements
Should not have
• Photos any mexican cliché

```html
<!DOCTYPE html>
<html lang="en">
<head>
<meta charset="utf-8">
<title>Bramwell Specialty Coffee – Dark Roast Label</title>
<link rel="stylesheet" href="https://fonts.googleapis.com/css2?family=Crimson+Text:wght@400;600&family=Lato:wght@700&display=swap">
<style>
  :root {
    --page: #ffffff;
    --lid: #5a2c1c;
    --cream: #e8dac6;
    --olive: #8f7b4f;
    --tan: #ccab86;
    --brown: #6f4230;
    --brown-deep: #6b4b40;
    --ink: #7a4632;
    --label-text: #ecdcc3;
  }
  * { margin: 0; padding: 0; box-sizing: border-box; }
  html, body {
    width: 1008px; height: 1200px; overflow: hidden;
    background: var(--page);
  }
  .canvas { position: relative; width: 1008px; height: 1200px; }
  .lid {
    position: absolute; left: 180px; top: 110px; width: 662px; height: 70px;
    background: var(--lid); border-radius: 10px;
  }
  .label {
    position: absolute; left: 192px; top: 160px; width: 638px; height: 880px;
    overflow: hidden;
  }
  .band { position: absolute; left: 0; width: 100%; }
  .band--cream { top: 0; height: 165px; background: var(--cream); }
  .band--olive { top: 165px; height: 180px; background: var(--olive); }
  .band--tan { top: 345px; height: 185px; background: var(--tan); }
  .band--brown { top: 530px; height: 175px; background: var(--brown); }
  .band--deep { top: 705px; height: 175px; background: var(--brown-deep); }
  .cup-art {
    position: absolute; left: 20px; top: 175px; width: 210px; height: 340px;
    border-radius: 40px 40px 100px 100px;
    background: radial-gradient(ellipse at 50% 60%, rgba(122,70,50,.55), rgba(122,70,50,.15) 70%, transparent);
  }
  .brand {
    position: absolute; left: 250px; top: 240px; width: 380px;
    font-family: "Crimson Text", serif; color: var(--ink);
  }
  .brand__name { font-size: 92px; font-weight: 400; line-height: 1; }
  .brand__tag {
    margin-top: 78px; margin-left: 60px;
    font-size: 44px; font-weight: 600; line-height: 1;
  }
  .product {
    position: absolute; left: 0; width: 100%;
    font-family: "Lato", sans-serif; font-weight: 700;
    color: var(--label-text); font-size: 96px; line-height: 1; letter-spacing: 1px;
  }
  .product--dark { top: 630px; left: 80px; }
  .product--roast { top: 715px; left: 240px; color: var(--tan); }
  .weight {
    position: absolute; left: 0; width: 100%; top: 820px; text-align: center;
    font-family: "Crimson Text", serif; font-weight: 600; font-size: 38px;
    color: var(--label-text); letter-spacing: 1px;
  }
</style>
</head>
<body>
<div class="canvas">
  <div class="lid"></div>
  <div class="label">
    <div class="band band--cream"></div>
    <div class="band band--olive"></div>
    <div class="band band--tan"></div>
    <div class="band band--brown"></div>
    <div class="band band--deep"></div>
    <div class="cup-art" role="img" aria-label="Illustration of a steaming coffee cup with arched detailing on a saucer"></div>
    <div class="brand">
      <div class="brand__name">Bramwell</div>
      <div class="brand__tag">Specialty Coffee</div>
    </div>
    <div class="product product--dark">DARK</div>
    <div class="product product--roast">ROAST</div>
    <div class="weight">NET WT 33.9 OZ(0.95kg)</div>
  </div>
</div>
</body>
</html>
```